Letterhead and business card design

We have recently had a logo designed by brandnestly. now we need a corporate identity with business card and lettehead design.

Target Market(s)

law firms corporates

Industry/Entity Type

Business

Requirements
Should not have
• cheesy detecive stuff like magnifying glasses etxcc

```html
<!DOCTYPE html>
<html lang="en">
<head>
<meta charset="utf-8">
<title>Harwell &amp; Lindqvist – Business Card</title>
<link rel="stylesheet" href="https://fonts.googleapis.com/css2?family=Cormorant+Garamond:ital,wght@0,500;1,500&family=Didact+Gothic&display=swap">
<style>
  :root {
    --stage: #4a4b4c;
    --card-dark-top: #7f8782;
    --card-dark-bottom: #545a58;
    --card-light: #f4f4f3;
    --ink-light: #f2f3f2;
    --ink-dark: #3c3f3f;
    --ink-muted: #4c4f50;
    --tab: #5f6462;
  }
  * { margin: 0; padding: 0; box-sizing: border-box; }
  html, body { width: 1200px; height: 1000px; overflow: hidden; }
  body {
    position: relative;
    background: var(--stage);
    font-family: "Didact Gothic", "Century Gothic", sans-serif;
  }
  .card {
    position: absolute;
    width: 531px;
    height: 302px;
    box-shadow: 0 4px 10px rgba(0,0,0,.35);
  }
  .card--front {
    left: 180px; top: 168px;
    background: linear-gradient(160deg, var(--card-dark-top), var(--card-dark-bottom));
    color: var(--ink-light);
  }
  .card--back {
    left: 472px; top: 550px;
    background: var(--card-light);
    color: var(--ink-dark);
  }
  .brand {
    position: absolute;
    left: 0; right: 0;
    text-align: center;
  }
  .card--front .brand { top: 94px; }
  .card--back .brand { top: 92px; }
  .brand__name {
    font-family: "Cormorant Garamond", Georgia, serif;
    font-weight: 500;
    font-size: 32px;
    letter-spacing: 1px;
    line-height: 1;
  }
  .brand__tagline {
    margin-top: 12px;
    font-family: "Cormorant Garamond", Georgia, serif;
    font-style: italic;
    font-size: 15px;
    letter-spacing: .3px;
  }
  .holder {
    position: absolute;
    top: 207px; left: 0; right: 0;
    text-align: center;
  }
  .holder__name { font-size: 15px; letter-spacing: .8px; }
  .holder__role { font-size: 12px; margin-top: 2px; }
  .side-tab {
    position: absolute;
    top: 93px;
    width: 14px; height: 55px;
    background: var(--tab);
  }
  .side-tab--left { left: 0; }
  .side-tab--right { right: 0; }
  .contact {
    position: absolute;
    top: 249px; left: 26px; right: 24px;
    display: flex;
    justify-content: space-between;
    font-size: 11.2px;
    line-height: 15px;
    color: var(--ink-muted);
  }
  .contact__item { display: flex; align-items: center; gap: 6px; }
  .contact__item svg { width: 9px; height: 9px; fill: var(--ink-muted); flex: none; }
</style>
</head>
<body>

<section class="card card--front">
  <div class="brand">
    <div class="brand__name">HARWELL &amp; LINDQVIST</div>
    <div class="brand__tagline">Investigations • Security • Intelligence</div>
  </div>
  <div class="holder">
    <div class="holder__name">MARCUS ELLERY</div>
    <div class="holder__role">Director</div>
  </div>
</section>

<section class="card card--back">
  <span class="side-tab side-tab--left"></span>
  <span class="side-tab side-tab--right"></span>
  <div class="brand">
    <div class="brand__name">HARWELL &amp; LINDQVIST</div>
    <div class="brand__tagline">Investigations • Security • Intelligence</div>
  </div>
  <div class="contact">
    <div class="contact__address">
      <div>PO Box 318, Harbour Street</div>
      <div>Wellington, New Zealand</div>
    </div>
    <div class="contact__web">
      <div class="contact__item">
        <svg viewBox="0 0 10 10"><rect x="0" y="2" width="10" height="6"/></svg>
        <span>marcus@harwellinquiry.co.nz</span>
      </div>
      <div class="contact__item">
        <svg viewBox="0 0 10 10"><circle cx="5" cy="5" r="4.5"/></svg>
        <span>www.harwellinquiry.co.nz</span>
      </div>
    </div>
    <div class="contact__phones">
      <div class="contact__item">
        <svg viewBox="0 0 10 10"><rect x="1" y="0" width="8" height="10" rx="1"/></svg>
        <span>+64 4 555 0142</span>
      </div>
      <div class="contact__item">
        <svg viewBox="0 0 10 10"><rect x="2" y="0" width="6" height="10" rx="1.5"/></svg>
        <span>+64 4 555 0187</span>
      </div>
    </div>
  </div>
</section>

</body>
</html>
```